Maple Gable Business Card

Colors can be blue, grey and white as you see in the attached logo. Needs to have a spot for name, title, phone, email, address, and website. There also needs to be a spot for an agent's picture.

Contact Information for Business Card

See project description.

Colors

Designer to choose colors to be used in the design.

```html
<!DOCTYPE html>
<html lang="en">
<head>
<meta charset="utf-8">
<title>Maple Gable Business Card</title>
<link href="https://fonts.googleapis.com/css2?family=Montserrat:wght@400;500;600&display=swap" rel="stylesheet">
<style>
  :root {
    --brand-blue: #2f74b5;
    --brand-blue-light: #4286c1;
    --brand-grey: #4a4a4c;
    --photo-tone-top: #c9d6e3;
    --photo-tone-bottom: #8fa9c2;
    --card-white: #ffffff;
    --backdrop: #2a2a2a;
  }
  * { margin: 0; padding: 0; box-sizing: border-box; }
  html, body {
    width: 1200px; height: 900px; overflow: hidden;
    background: var(--backdrop);
    font-family: "Montserrat", sans-serif;
  }
  .stage { position: relative; width: 1200px; height: 900px; }
  .card {
    position: absolute; left: 250px; width: 700px; height: 400px;
    overflow: hidden;
    box-shadow: 0 10px 30px rgba(0,0,0,0.5);
  }
  .card-front {
    top: 30px;
    background: linear-gradient(135deg, var(--brand-blue) 0%, var(--brand-blue-light) 100%);
    display: flex; align-items: center; justify-content: center;
    padding-bottom: 20px;
  }
  .brand-name {
    display: flex; align-items: center; gap: 14px;
    font-weight: 600; text-transform: uppercase; letter-spacing: 1px;
    white-space: nowrap;
  }
  .brand-name .brand-square { display: block; flex: none; }
  .card-front .brand-name { color: var(--card-white); font-size: 38px; }
  .card-front .brand-square { width: 22px; height: 22px; background: var(--card-white); }

  .card-back { top: 470px; background: var(--card-white); }
  .agent { position: absolute; top: 30px; left: 0; padding-left: 36px; }
  .agent::before {
    content: ""; position: absolute; left: 0; top: 2px;
    width: 10px; height: 44px; background: var(--brand-blue);
  }
  .agent-name {
    color: var(--brand-blue); font-weight: 600; font-size: 26px;
    letter-spacing: 1.5px; text-transform: uppercase; line-height: 1.1;
  }
  .agent-title { color: var(--brand-grey); font-size: 16px; margin-top: 2px; }

  .agent-photo {
    position: absolute; left: 36px; top: 100px; width: 120px; height: 150px;
    background: linear-gradient(180deg, var(--photo-tone-top) 0%, var(--photo-tone-bottom) 100%);
    border-bottom: 4px solid var(--brand-blue);
  }

  .card-back .brand-name {
    position: absolute; right: 50px; top: 160px;
    color: var(--brand-blue); font-size: 40px;
  }
  .card-back .brand-square { width: 26px; height: 26px; background: var(--brand-blue); }

  .contact-band {
    position: absolute; left: 0; right: 0; bottom: 0; height: 130px;
    background: var(--brand-blue); color: var(--card-white);
  }
  .contact-list {
    position: absolute; left: 32px; top: 20px; list-style: none;
    font-size: 18px; letter-spacing: 1px; line-height: 30px;
  }
  .contact-list li { display: flex; align-items: center; gap: 12px; }
  .contact-list svg { width: 16px; height: 16px; flex: none; }
  .contact-list strong { font-weight: 600; }
  .office-address {
    position: absolute; right: 32px; bottom: 18px; text-align: right;
    font-style: normal; font-size: 18px; letter-spacing: 1.5px; line-height: 30px;
  }
</style>
</head>
<body>
<main class="stage">
  <section class="card card-front">
    <div class="brand-name"><span class="brand-square"></span>Maple Gable</div>
  </section>

  <section class="card card-back">
    <header class="agent">
      <h1 class="agent-name">Owen Hartley</h1>
      <p class="agent-title">Director</p>
    </header>

    <div class="agent-photo" role="img" aria-label="Agent portrait photo"></div>

    <div class="brand-name"><span class="brand-square"></span>Maple Gable</div>

    <footer class="contact-band">
      <ul class="contact-list">
        <li>
          <svg viewBox="0 0 16 16" aria-hidden="true"><path d="M4 1.5 L6.5 4.5 L5 6.5 C6 8.5 7.5 10 9.5 11 L11.5 9.5 L14.5 12 L12.5 14.5 C7 13.5 2.5 9 1.5 3.5 Z" fill="none" stroke="currentColor" stroke-width="1.4" stroke-linejoin="round"/></svg>
          (555) 214-3086
        </li>
        <li>
          <svg viewBox="0 0 16 16" aria-hidden="true"><rect x="1.5" y="3.5" width="13" height="9" fill="none" stroke="currentColor" stroke-width="1.4"/><path d="M1.5 3.5 L8 9 L14.5 3.5" fill="none" stroke="currentColor" stroke-width="1.4"/></svg>
          info@maplegable.com
        </li>
        <li>
          <svg viewBox="0 0 16 16" aria-hidden="true"><g fill="none" stroke="currentColor" stroke-width="1.3"><circle cx="8" cy="8" r="6.5"/><ellipse cx="8" cy="8" rx="3" ry="6.5"/><line x1="1.5" y1="8" x2="14.5" y2="8"/><line x1="2.5" y1="4.5" x2="13.5" y2="4.5"/><line x1="2.5" y1="11.5" x2="13.5" y2="11.5"/></g></svg>
          <span>www.<strong>maplegable</strong>.com</span>
        </li>
      </ul>
      <address class="office-address">718 Cedar Bluff Drive<br>Reno, NV 89502</address>
    </footer>
  </section>
</main>
</body>
</html>
```